Web portal for events

The project is about creating a web application - portal for culture events in Denmark.

Design

We aim for very simplistic, light and fully responsive design. The white background is preferable, as well as light color tones. As inspirational points we like the colors used in www.parvolio.com and www.brindlemoor.org

FORMAT AND REQUIREMENTS:
1. Design should be provided based on the wireframes specified as a link below.
2. The design (and all of its pages) should be provided in three resolution variants:
- Desktop
- Tablet
- Phone
3. The design should be provided as PSD, where each page/section should be in its own PSD file
4. All graphical elements in the design should be delivered as single layers which can then be extracted from the PSD.
5. All graphical elements (icons, graphical buttons, etc.) should be provided as vector objects in the PSD, so that they can be exported into different sizes without loss of quality (for responsiveness)
6. The design should use either web safe fonts or Google Fonts.

RESPONSIVENESS
The web application should be visible on any devices (i.e. responsive design)

WIREFRAMES:
https://velkotrams.examplewire.com/projects/fennoplex/prototype/Homepage?key=3b7c19d0f2a84e6c5d1e9a07b4f2c8d6e1a3f590

We expect design of the following wireframes:

Homepage:
https://velkotrams.examplewire.com/projects/fennoplex/Homepage

For arrangører - billede uploaded:
https://velkotrams.examplewire.com/projects/fennoplex/For%20arrang%C3%B8rer%20-%20billede%20uploaded

Further specifications of the project (i.e. functionality, etc.):
https://files.quorvane.net/document/d/8pKw_Rt2mZqLx4NvB7yHc0aEs9uGdJf3TiOb6nVlW1k/edit?usp=sharing

```html
<!DOCTYPE html>
<html lang="da">
<head>
<meta charset="utf-8">
<title>KULTRO – Din Guide til kultur og events</title>
<link rel="stylesheet" href="https://fonts.googleapis.com/css2?family=Lato:wght@400;700&family=Montserrat:wght@400;700&display=swap">
<style>
:root{
  --brand:#fb4214;
  --brand-deep:#e2390f;
  --ink:#1f1f1f;
  --dark-btn:#2b1a12;
  --cta:#e3121b;
  --band:#efefef;
  --line:#d9d9d9;
  --muted:#8a8a8a;
  --white:#ffffff;
}
*{box-sizing:border-box;margin:0;padding:0}
html,body{width:1200px;height:1140px;overflow:hidden;background:var(--white);font-family:"Lato",Arial,sans-serif;color:var(--ink)}
.page{position:relative;width:1200px;height:1140px}

/* header */
.site-header{position:absolute;top:0;left:0;width:1200px;height:90px;background:var(--brand)}
.brand{position:absolute;left:180px;top:0;width:170px;height:90px;background:var(--brand-deep);padding:20px 0 0 7px;color:var(--white);font-family:"Montserrat",Arial,sans-serif}
.brand-name{font-size:20px;font-weight:400;letter-spacing:1px;line-height:22px}
.brand-tag{font-size:10px;font-weight:700;margin-top:5px}
.search{position:absolute;left:362px;top:28px;width:442px;height:34px;background:var(--white);border:3px solid #ffd9cc;border-radius:18px;display:flex;align-items:center;padding-left:14px;font-size:12px;color:#9a9a9a;gap:8px}
.btn-dark{background:var(--dark-btn);color:var(--white);display:flex;align-items:center;justify-content:center}
.search-btn{position:absolute;left:815px;top:31px;width:55px;height:30px;font-size:12px;font-weight:700;font-family:"Montserrat",Arial,sans-serif}
.advanced-btn{position:absolute;left:883px;top:31px;width:136px;height:30px;font-size:12px;font-family:"Montserrat",Arial,sans-serif}
.login-btn{position:absolute;left:1092px;top:0;width:88px;height:32px;font-size:11px}

/* category nav */
.category-nav{position:absolute;top:90px;left:0;width:1200px;height:58px;background:var(--band);border-bottom:1px solid var(--line)}
.category-nav ul{list-style:none;display:flex;position:absolute;left:180px;top:22px;gap:0}
.category-nav li{font-size:12px;height:22px;line-height:22px;margin-right:37px}
.category-nav li.active{background:var(--ink);color:var(--white);border-radius:12px;padding:0 9px;margin-right:27px}

/* events */
.events-head{position:absolute;left:180px;top:171px;display:flex;align-items:center;font-size:12px}
.section-title{color:var(--brand);font-size:12px;font-weight:400;margin-right:30px}
.sort-label{margin-right:10px}
.sort-opt{height:19px;padding:0 9px;display:flex;align-items:center;background:#e2e2e2;border:1px solid #cfcfcf;margin-right:8px;font-size:12px;color:#333}
.sort-opt.active{background:var(--ink);color:var(--white);border-color:var(--ink)}
.event-grid{position:absolute;left:180px;top:219px;display:grid;grid-template-columns:repeat(3,196px);column-gap:27px;row-gap:32px}
.event-card{width:196px;height:165px}
.event-media{height:86px}
.event-title{color:var(--brand);font-size:14px;font-weight:400;margin-top:10px;line-height:17px}
.event-meta{display:flex;justify-content:space-between;font-size:10px;margin-top:5px}
.event-actions{display:flex;justify-content:space-between;margin-top:9px}
.event-actions span{height:25px;display:flex;align-items:center;justify-content:center;font-size:11px;color:var(--white)}
.see-btn{width:63px;background:var(--ink)}
.fav-btn{width:127px;background:var(--cta)}

.g1{background:linear-gradient(160deg,#f4c21a,#c8620a 50%,#1e0c04)}
.g2{background:linear-gradient(150deg,#2a1f45,#b23b8e 50%,#3a2d3f)}
.g3{background:linear-gradient(180deg,#8ab2d8 0%,#d98a3e 50%,#a63a24)}
.g4{background:linear-gradient(150deg,#3a2215,#d9a07c 50%,#5a3020)}
.g5{background:linear-gradient(180deg,#2b3f8c,#6a3a5c 60%,#d8902e)}
.g6{background:linear-gradient(150deg,#8fa3c8,#e9c8b4 50%,#5a6fa6)}
.g7{background:linear-gradient(180deg,#e9d27a,#7a7a3a 55%,#303628)}
.g8{background:linear-gradient(150deg,#6a0a10,#e2304a 50%,#f0b08a)}
.g9{background:linear-gradient(180deg,#3c7ed0,#6f7f7a 55%,#2b6aa6)}
.g10{background:linear-gradient(150deg,#2a3a6a,#e07a8a 50%,#2a2030)}
.g11{background:linear-gradient(180deg,#2f6fd0,#a9c6e6 60%,#c9b264)}
.g12{background:linear-gradient(180deg,#3e8fd4,#9fc4e4 60%,#6a5a48)}

.pager{position:absolute;left:574px;top:1009px;font-size:12px;display:flex;gap:7px}
.pager .current{color:var(--brand)}

/* sidebar */
.divider{position:absolute;left:844px;top:171px;width:1px;height:815px;background:var(--line)}
.sidebar{position:absolute;left:862px;top:171px;width:158px}
.sidebar-title{color:var(--brand);font-size:12px;font-weight:400}
.fav-list{margin-top:38px;display:flex;flex-direction:column;gap:13px}
.fav-list div{height:86px}
.f1{background:linear-gradient(180deg,#dfe6ee,#c9a24a 50%,#8c8a84)}
.f2{background:linear-gradient(180deg,#7aa6d6,#b56a3e 60%,#6a5a4a)}
.f3{background:linear-gradient(180deg,#4f8ad0,#9a7a6a 60%,#3a4a4a)}
.see-fav{margin-top:17px;width:106px;height:25px;background:var(--ink);color:var(--white);font-size:11px;display:flex;align-items:center;justify-content:center}
.newsletter-title{color:var(--brand);font-size:15px;font-weight:400;margin-top:23px}
.newsletter-text{color:var(--muted);font-size:11.5px;line-height:14.5px;margin-top:14px}
.email-field{margin-top:20px;height:32px;border:1px solid var(--line);font-size:11.5px;color:#9a9a9a;padding-left:9px;display:flex;align-items:center}
.submit-btn{margin-top:10px;width:55px;height:25px;background:var(--ink);color:var(--white);font-size:11px;display:flex;align-items:center;justify-content:center}

/* footer */
.site-footer{position:absolute;left:0;top:1049px;width:1200px;height:91px;background:var(--brand);color:var(--white);font-size:11.5px}
.footer-links{position:absolute;left:180px;top:27px;display:flex;gap:9px}
.copyright{position:absolute;left:181px;top:52px}
</style>
</head>
<body>
<div class="page">
  <header class="site-header">
    <div class="brand"><div class="brand-name">KULTRO</div><div class="brand-tag">Din Guide til kultur og events</div></div>
    <div class="search">
      <svg width="13" height="13" viewBox="0 0 13 13"><circle cx="5.5" cy="5.5" r="4.3" fill="none" stroke="#9a9a9a" stroke-width="1.5"/><line x1="8.6" y1="8.6" x2="12" y2="12" stroke="#9a9a9a" stroke-width="1.6"/></svg>
      Search
    </div>
    <div class="btn-dark search-btn">SOG</div>
    <div class="btn-dark advanced-btn">Avanceret Sogning</div>
    <div class="btn-dark login-btn">Login/Signup</div>
  </header>

  <nav class="category-nav">
    <ul>
      <li class="active">ALL</li><li>MUSIC</li><li>SPORT</li><li>TEATER</li><li>UPCOMING</li><li>OLDER</li><li>BORN</li><li>MOTION</li><li>DIVERSE</li>
    </ul>
  </nav>

  <div class="events-head">
    <h2 class="section-title">POPULAR EVENTS</h2>
    <span class="sort-label">Sorter After</span>
    <span class="sort-opt active">Popular</span>
    <span class="sort-opt"><svg width="28" height="8" viewBox="0 0 28 8"><g fill="#555"><rect x="2" y="1" width="2" height="2"/><rect x="5" y="1" width="2" height="2"/><rect x="8" y="1" width="2" height="2"/><rect x="2" y="5" width="2" height="2"/><rect x="5" y="5" width="2" height="2"/><rect x="8" y="5" width="2" height="2"/><rect x="17" y="1" width="2" height="1.5"/><rect x="20" y="1" width="6" height="1.5"/><rect x="17" y="5" width="2" height="1.5"/><rect x="20" y="5" width="6" height="1.5"/></g></svg></span>
    <span class="sort-opt">Date&nbsp;<svg width="7" height="6" viewBox="0 0 7 6"><path d="M0 0h7L3.5 6z" fill="#222"/></svg></span>
    <span class="sort-opt">Prize</span>
  </div>

  <main class="event-grid">
    <article class="event-card"><div class="event-media g1" role="img" aria-label="Koncertpublikum foran scenelys"></div><h3 class="event-title">Aksel Vinter Koncert</h3><div class="event-meta"><span>Oplev XXXX......</span><span>20/2/2014</span></div><div class="event-actions"><span class="see-btn">Se Event</span><span class="fav-btn">Tilfoj til mine favoritter</span></div></article>
    <article class="event-card"><div class="event-media g2" role="img" aria-label="Festscene med konfetti"></div><h3 class="event-title">Aksel Vinter Koncert</h3><div class="event-meta"><span>Oplev XXXX......</span><span>20/2/2014</span></div><div class="event-actions"><span class="see-btn">Se Event</span><span class="fav-btn">Tilfoj til mine favoritter</span></div></article>
    <article class="event-card"><div class="event-media g3" role="img" aria-label="Farverige huse ved en kanal"></div><h3 class="event-title">Aksel Vinter Koncert</h3><div class="event-meta"><span>Oplev XXXX......</span><span>20/2/2014</span></div><div class="event-actions"><span class="see-btn">Se Event</span><span class="fav-btn">Tilfoj til mine favoritter</span></div></article>
    <article class="event-card"><div class="event-media g4" role="img" aria-label="Dansende festdeltagere"></div><h3 class="event-title">Aksel Vinter Koncert</h3><div class="event-meta"><span>Oplev XXXX......</span><span>20/2/2014</span></div><div class="event-actions"><span class="see-btn">Se Event</span><span class="fav-btn">Tilfoj til mine favoritter</span></div></article>
    <article class="event-card"><div class="event-media g5" role="img" aria-label="Oplyst forlystelsespark om aftenen"></div><h3 class="event-title">Aksel Vinter Koncert</h3><div class="event-meta"><span>Oplev XXXX......</span><span>20/2/2014</span></div><div class="event-actions"><span class="see-btn">Se Event</span><span class="fav-btn">Tilfoj til mine favoritter</span></div></article>
    <article class="event-card"><div class="event-media g6" role="img" aria-label="Venner der synger karaoke"></div><h3 class="event-title">Aksel Vinter Koncert</h3><div class="event-meta"><span>Oplev XXXX......</span><span>20/2/2014</span></div><div class="event-actions"><span class="see-btn">Se Event</span><span class="fav-btn">Tilfoj til mine favoritter</span></div></article>
    <article class="event-card"><div class="event-media g7" role="img" aria-label="Byens skyline i solnedgang"></div><h3 class="event-title">Aksel Vinter Koncert</h3><div class="event-meta"><span>Oplev XXXX......</span><span>20/2/2014</span></div><div class="event-actions"><span class="see-btn">Se Event</span><span class="fav-btn">Tilfoj til mine favoritter</span></div></article>
    <article class="event-card"><div class="event-media g8" role="img" aria-label="Dansende på natklub i rødt lys"></div><h3 class="event-title">Aksel Vinter Koncert</h3><div class="event-meta"><span>Oplev XXXX......</span><span>20/2/2014</span></div><div class="event-actions"><span class="see-btn">Se Event</span><span class="fav-btn">Tilfoj til mine favoritter</span></div></article>
    <article class="event-card"><div class="event-media g9" role="img" aria-label="Fjeld ved en blå fjord"></div><h3 class="event-title">Aksel Vinter Koncert</h3><div class="event-meta"><span>Oplev XXXX......</span><span>20/2/2014</span></div><div class="event-actions"><span class="see-btn">Se Event</span><span class="fav-btn">Tilfoj til mine favoritter</span></div></article>
    <article class="event-card"><div class="event-media g10" role="img" aria-label="DJ-pult og dansegulv"></div><h3 class="event-title">Aksel Vinter Koncert</h3><div class="event-meta"><span>Oplev XXXX......</span><span>20/2/2014</span></div><div class="event-actions"><span class="see-btn">Se Event</span><span class="fav-btn">Tilfoj til mine favoritter</span></div></article>
    <article class="event-card"><div class="event-media g11" role="img" aria-label="Fyrtårn og gule huse under blå himmel"></div><h3 class="event-title">Aksel Vinter Koncert</h3><div class="event-meta"><span>Oplev XXXX......</span><span>20/2/2014</span></div><div class="event-actions"><span class="see-btn">Se Event</span><span class="fav-btn">Tilfoj til mine favoritter</span></div></article>
    <article class="event-card"><div class="event-media g12" role="img" aria-label="Luftballon over klippelandskab"></div><h3 class="event-title">Aksel Vinter Koncert</h3><div class="event-meta"><span>Oplev XXXX......</span><span>20/2/2014</span></div><div class="event-actions"><span class="see-btn">Se Event</span><span class="fav-btn">Tilfoj til mine favoritter</span></div></article>
  </main>

  <div class="pager"><span class="current">1</span><span>|</span><span>2</span><span>|</span><span>3</span></div>

  <div class="divider"></div>
  <aside class="sidebar">
    <h2 class="sidebar-title">MINE FAVORITTER</h2>
    <div class="fav-list">
      <div class="f1" role="img" aria-label="Brostensgade med gule huse"></div>
      <div class="f2" role="img" aria-label="Gammel lade ved kysten"></div>
      <div class="f3" role="img" aria-label="Slot med tårne og rytterstatue"></div>
    </div>
    <div class="see-fav">Se mine Favoritter</div>
    <h2 class="newsletter-title">NYHEDSBREV</h2>
    <p class="newsletter-text">Neque porro quisquam est qui dolorem ipsum quia dolor sit amet, consectetur, adipisci velit...</p>
    <div class="email-field">Email Address</div>
    <div class="submit-btn">Submit</div>
  </aside>

  <footer class="site-footer">
    <div class="footer-links"><span>Om Kultro</span><span>|</span><span>Vilkar &amp; betingelser</span><span>|</span><span>Kobspolitik</span><span>|</span><span>Nyhedsbrev</span><span>|</span><span>Kontakt</span><span>|</span><span>Login/Register</span><span>|</span><span>Hjaelp</span><span>|</span><span>For Arrangorer</span><span>|</span><span>For Kommuner og Turistforeninger</span></div>
    <div class="copyright">Copyright © 2014 KULTRO. All rights reserved.</div>
  </footer>
</div>
</body>
</html>
```